Coastal Learner Bureau business cards

Australian company about to start offering its services. We recruit international students to come to study English, vocational education and postgraduate courses in Australia. We help them find the institution and select the right city they want to come to Australia. We are a young, online oriented and supportive agency. Our clients are between 18 and 35 years old, mainly University students, young professionals or people with work experience. We provide much more information that any other agency offer. We administrate a Facebook group with more than 11.000 members that daily ask questions about general information when coming to Australia, while they are here and even after they leave the country

Target Market(s)

International students from South America, Central America and Europe

Industry/Entity Type

Student

Contact Information for Business Card

Tomas Bilbrea
Managing Director
tomas@kelvarin.com.au
www.kelvoria.com.au
+61 491058264
Melbourne, Australia

Font styles to use
Serif
Sans Serif

Colors

Designer to choose colors to be used in the design.

Requirements
Must have
• Horizontal design
• Standard business card size and shape. If font uses green or yellow colours, they will have to match the ones from the logo
Nice to have
• UPDATE: Use the contents of the green image to design one of the card sides. Use our logo in the background of that side as watermark.
• Passport image, or immigration stamps. A picture of the Yarra River (from Melbourne) would be cool as well.
Should not have
• Non-standard business card size and shape
• Not black as the background colour of any sides as we are not a VIP agency or a hight class service. We are orientes to young people and they like colours, pictures, something attractive.
• Vertical design
• NO YELLOW or BLACK AS THE BACKGROUND COLOUR OF ANY SIDE OF THE BIZ CARD

```html
<!DOCTYPE html>
<html lang="en">
<head>
<meta charset="utf-8">
<title>Coastal Learner Bureau business cards</title>
<link rel="stylesheet" href="https://fonts.googleapis.com/css2?family=Roboto:wght@400;500;700&display=swap">
<style>
  :root {
    --green: #0c6440;
    --green-deep: #0a5636;
    --gold: #e8b51f;
    --white: #ffffff;
    --ink-soft: #1d2b24;
    --stage: #6b7478;
  }
  * { margin: 0; padding: 0; box-sizing: border-box; }
  html, body { width: 1200px; height: 900px; overflow: hidden; }
  body {
    background: var(--stage);
    font-family: "Roboto", Arial, sans-serif;
    position: relative;
  }
  .card {
    position: absolute;
    left: 285px;
    width: 630px;
    height: 360px;
    border-radius: 18px;
    overflow: hidden;
  }
  .card--front { top: 50px; background: var(--white); }
  .card--back { top: 470px; background: var(--green); }
  .card__art { position: absolute; inset: 0; width: 100%; height: 100%; }

  .brand {
    position: absolute;
    display: flex;
    align-items: center;
    gap: 12px;
    font-weight: 700;
    letter-spacing: 0.5px;
  }
  .brand__dot { border-radius: 50%; background: var(--gold); flex: none; }
  .card--front .brand { left: 58px; top: 48px; color: var(--green); font-size: 40px; }
  .card--front .brand__dot { width: 22px; height: 22px; }
  .card--back .brand {
    left: 0; right: 0; top: 128px; justify-content: center;
    color: var(--white); font-size: 64px;
  }
  .card--back .brand__dot { width: 32px; height: 32px; }

  .badge {
    position: absolute; left: 30px; top: 196px;
    width: 44px; height: 44px; border-radius: 50%;
    border: 2px solid rgba(255,255,255,0.75);
    background: rgba(255,255,255,0.12);
  }

  .person { position: absolute; right: 44px; top: 128px; text-align: right; }
  .person__name { color: var(--green); font-size: 26px; font-weight: 700; }
  .person__role { color: var(--ink-soft); font-size: 11px; font-weight: 500; margin-top: 2px; }

  .contact {
    position: absolute; right: 36px; top: 262px;
    list-style: none; color: var(--white); font-size: 15px; line-height: 22px;
  }
  .contact li { display: flex; justify-content: flex-end; align-items: center; gap: 10px; }
  .contact svg { width: 14px; height: 14px; flex: none; }
  .contact .spacer { width: 14px; }

  .url {
    position: absolute; left: 0; right: 0; top: 228px;
    text-align: center; color: var(--white); font-size: 18px; letter-spacing: 0.4px;
  }
</style>
</head>
<body>

<section class="card card--front" aria-label="Business card front">
  <svg class="card__art" viewBox="0 0 630 360" preserveAspectRatio="none" aria-hidden="true">
    <path d="M0 132 C 120 236, 330 214, 630 252 L630 360 L0 360 Z" fill="var(--green)"/>
    <path d="M60 92 C 90 200, 330 212, 575 244" fill="none" stroke="var(--gold)" stroke-width="3"/>
    <path d="M0 150 C 90 220, 250 225, 420 230" fill="none" stroke="var(--white)" stroke-width="5" opacity="0.9"/>
  </svg>

  <div class="brand"><span class="brand__dot"></span>Kelvoria</div>
  <div class="badge" role="img" aria-label="Partner badge"></div>

  <div class="person">
    <div class="person__name">Tomas Bilbrea</div>
    <div class="person__role">Managing Director</div>
  </div>

  <ul class="contact">
    <li>Melbourne, Australia <span class="spacer"></span></li>
    <li>+61 491058264
      <svg viewBox="0 0 24 24"><path fill="#fff" d="M6.6 10.8a15 15 0 0 0 6.6 6.6l2.2-2.2a1 1 0 0 1 1-.25 11.4 11.4 0 0 0 3.6.57 1 1 0 0 1 1 1V20a1 1 0 0 1-1 1A17 17 0 0 1 3 4a1 1 0 0 1 1-1h3.5a1 1 0 0 1 1 1c0 1.25.2 2.45.57 3.57a1 1 0 0 1-.25 1z"/></svg>
    </li>
    <li>tomas@kelvarin.com.au
      <svg viewBox="0 0 24 24"><path fill="#fff" d="M3 5h18v14H3z"/><path d="M3 5l9 8 9-8" fill="none" stroke="var(--green)" stroke-width="2"/></svg>
    </li>
    <li>www.kelvoria.com.au
      <svg viewBox="0 0 24 24"><circle cx="12" cy="12" r="9" fill="none" stroke="#fff" stroke-width="2"/><path d="M3 12h18M12 3c3 3 3 15 0 18M12 3c-3 3-3 15 0 18" fill="none" stroke="#fff" stroke-width="1.6"/></svg>
    </li>
  </ul>
</section>

<section class="card card--back" aria-label="Business card back">
  <div class="brand"><span class="brand__dot"></span>Kelvoria</div>
  <div class="url">www.kelvoria.com.au</div>
</section>

</body>
</html>
```